Business Card for a mobile physiotherapy company

I need a layout for a business card for a mobile physiotherapy company.
Slogan is "Mobile Physiotherapy - Your Road To Recovery"
Phone number is 867-555-0142
Email VardenTherapy@postnest.ca (subject to change with website)
Website www.VardenTherapy.ca
My name and credentials: Luke Varden Luke Varden, BSc(kin), MPT, CAFCI, IMS
Information maybe included: Direct Billing, Services including Physiotherapy, IMS, acupuncture
Maybe include facebook and instagram logos
One side with the logo clean and sharp
Other side with details, try not to look too busy, keep everything concise

```html
<!DOCTYPE html>
<html lang="en">
<head>
<meta charset="utf-8">
<title>Varden Therapy – Business Card</title>
<link href="https://fonts.googleapis.com/css2?family=Bebas+Neue&family=Lato:ital,wght@0,400;0,700;1,400;1,700&display=swap" rel="stylesheet">
<style>
  :root {
    --canvas-bg: #e4e2df;
    --navy: #2a4672;
    --navy-deep: #1d3761;
    --card-white: #f4f4f4;
    --text-grey: #6f7276;
    --silver: #c9ccd0;
    --tagline-green: #1f4a3c;
  }
  * { margin: 0; padding: 0; box-sizing: border-box; }
  html, body { width: 1200px; height: 960px; overflow: hidden; }
  body {
    position: relative;
    background: var(--canvas-bg);
    font-family: "Lato", sans-serif;
  }
  .card {
    position: absolute;
    left: 295px;
    width: 615px;
    height: 352px;
  }
  .card-front {
    top: 103px;
    background: linear-gradient(160deg, #2f4f7a 0%, var(--navy-deep) 100%);
    display: flex;
    flex-direction: column;
    align-items: center;
    justify-content: center;
    color: var(--silver);
  }
  .brand-mark {
    width: 14px; height: 14px;
    border-radius: 50%;
    background: var(--silver);
    margin-bottom: 26px;
  }
  .brand-name {
    font-family: "Lato", sans-serif;
    font-weight: 400;
    text-align: center;
    line-height: 1;
  }
  .brand-name .primary { display: block; font-size: 52px; letter-spacing: 6px; }
  .brand-name .secondary { display: block; font-size: 22px; letter-spacing: 9px; margin-top: 16px; }

  .card-back {
    top: 508px;
    background: var(--card-white);
  }
  .accent-bar {
    position: absolute;
    left: 0; top: 52px;
    width: 16px; height: 52px;
    background: var(--navy);
  }
  .holder-name {
    position: absolute;
    left: 47px; top: 56px;
    font-family: "Bebas Neue", sans-serif;
    font-size: 29px;
    color: var(--navy);
    letter-spacing: 0.3px;
  }
  .credentials {
    position: absolute;
    left: 47px; top: 86px;
    font-size: 14px;
    color: var(--text-grey);
  }
  .services {
    position: absolute;
    left: 47px; top: 156px;
    list-style: none;
    font-size: 14.5px;
    line-height: 18px;
    color: var(--text-grey);
  }
  .tagline-row {
    position: absolute;
    left: 47px; right: 42px; top: 221px;
    display: flex;
    align-items: center;
    font-size: 14px;
    font-style: italic;
  }
  .tagline-rule { width: 234px; height: 2px; background: var(--navy); margin-right: 6px; }
  .tagline-main { font-weight: 700; color: var(--navy); }
  .tagline-sep { margin: 0 8px; color: var(--navy); font-style: normal; font-weight: 700; }
  .tagline-sub { color: var(--tagline-green); }
  .contacts {
    position: absolute;
    left: 47px; top: 253px;
    list-style: none;
    font-size: 14.5px;
    line-height: 18px;
    color: var(--text-grey);
  }
  .contacts li { display: flex; align-items: center; }
  .contact-icon { width: 11px; height: 11px; margin-right: 8px; fill: none; stroke: var(--navy); stroke-width: 1.4; }
  .social-dot { width: 11px; height: 11px; border-radius: 50%; background: var(--navy); margin-right: 8px; }
</style>
</head>
<body>
  <section class="card card-front" aria-label="Card front">
    <div class="brand-mark"></div>
    <div class="brand-name">
      <span class="primary">VARDEN</span>
      <span class="secondary">THERAPY</span>
    </div>
  </section>

  <section class="card card-back" aria-label="Card back">
    <div class="accent-bar"></div>
    <h1 class="holder-name">Luke Varden Luke Varden</h1>
    <p class="credentials">BSc (kin), MPT, CAFCI, IMS</p>
    <ul class="services">
      <li>• Direct Billing</li>
      <li>• Services including Physiotherapy</li>
      <li>• IMS • Acupuncture</li>
    </ul>
    <div class="tagline-row">
      <span class="tagline-rule"></span>
      <span class="tagline-main">Mobile Physiotherapy</span>
      <span class="tagline-sep">|</span>
      <span class="tagline-sub">Your Road To Recovery</span>
    </div>
    <ul class="contacts">
      <li><svg class="contact-icon" viewBox="0 0 12 12"><path d="M2.5 1.5 L4.5 1.5 L5.2 3.8 L4 4.8 Q5 7 7.2 8 L8.2 6.8 L10.5 7.5 L10.5 9.5 Q10 10.5 9 10.5 Q1.5 10 1.5 3 Q1.5 2 2.5 1.5 Z"/></svg>867-555-0142</li>
      <li><svg class="contact-icon" viewBox="0 0 12 12"><rect x="1" y="2.5" width="10" height="7"/><path d="M1 2.5 L6 6.5 L11 2.5"/></svg>VardenTherapy@postnest.ca</li>
      <li><svg class="contact-icon" viewBox="0 0 12 12"><circle cx="6" cy="6" r="5"/><ellipse cx="6" cy="6" rx="2.2" ry="5"/><path d="M1 6 H11"/></svg>www.VardenTherapy.ca</li>
      <li><span class="social-dot"></span>VardenTherapy</li>
    </ul>
  </section>
</body>
</html>
```